Vorelan.com Personal Trainer/Fitness Website

I want a website to market my personal training/Outdoor Bootcamp Class services, as well as to ditribute nutrivex. I need a logo as well I included an address for the Harbor Gales 1975 logo. I'd like Vorelan in place of Harbor Gales, and in Black and white, just different enough so I can't get sued by the PBL.
https://www.pictofind.example/imgres?imgurl=http%3A%2F%2Fwww.darnell-quibury.example%2Fwp-content%2Fuploads%2F2014%2F01%2Fgales_logo4.jpg&imgrefurl=http%3A%2F%2Fwww.darnell-quibury.example%2Fpbl-logo-redesigns-harbor-gales%2F&docid=_qkwzR7TBAgXpL&tbnid=m4tpU8KdOXjnRP%3A&w=600&h=450&client=ms-android-carrier&bih=512&biw=360&ved=0ahUKEwiRtpgyp9HMAhUTwGMKHRPMBWMQMwg6KBQwFA&iact=mrc&uact=8.
It should be about 5 pages 1. home 2. about 3. Services 4. Blog/Videos and programs 5. Contact.
http://www.dorvinfitness.example.uk/ is a website I like the style of.

Target Market(s)

Seattle area

Industry/Entity Type

Fitness

Coding

Coded - Design and coding required

Number of Pages Required

4 page

Font styles to use
Serif
Sans Serif

Requirements
Must have
• A minimal look
Nice to have
• A logo similar to the 1975 Harbor Galewinds Logo, with a Small Milo Brandt ripping his shirt open(with a picture of the logo on his shirt, picture within picture) to turn into Ironjaw in the center. Skyline is black, Background and small figure white(with black logo on shirt)

```html
<!DOCTYPE html>
<html lang="en">
<head>
<meta charset="utf-8">
<title>Vorelan – Personal Training</title>
<link href="https://fonts.googleapis.com/css2?family=Roboto+Condensed:wght@400;700&family=Open+Sans:ital,wght@0,400;0,600;1,400&display=swap" rel="stylesheet">
<style>
:root{
  --green:#1f6f3b;
  --green-dark:#175a2f;
  --yellow:#f3c317;
  --ink:#333;
  --muted:#666;
  --light:#f4f4f4;
  --footer:#2a2a2a;
  --white:#fff;
  --icon-grey:#888;
}
*{box-sizing:border-box;margin:0;padding:0}
html,body{width:1200px;height:2970px;overflow:hidden}
body{font-family:"Open Sans",sans-serif;color:var(--ink);background:var(--white);position:relative}
.heading{font-family:"Roboto Condensed",sans-serif;text-transform:uppercase;font-weight:400;color:#222}
a{color:inherit;text-decoration:none}

/* header */
.site-header{position:absolute;top:0;left:0;width:1200px;height:120px;background:linear-gradient(#fff,#f2f2f2);border-bottom:1px solid #e3e3e3}
.brand{position:absolute;left:100px;top:8px;width:100px;display:flex;flex-direction:column;align-items:center;gap:4px}
.brand-mark{width:64px;height:64px;border-radius:50%;background:#1c1c1c}
.brand-name{font-family:"Roboto Condensed",sans-serif;font-weight:700;font-size:27px;line-height:1;color:#222;letter-spacing:.5px}
.topbar{position:absolute;right:100px;top:8px;display:flex;align-items:center;gap:28px;font-size:12px;color:#333}
.topbar span{display:flex;align-items:center;gap:8px}
.social-dots{display:flex;gap:5px}
.social-dots i{width:18px;height:18px;border-radius:50%;background:var(--yellow);display:block}
.main-nav{position:absolute;right:100px;top:74px;display:flex;gap:34px;font-family:"Roboto Condensed",sans-serif;font-size:14px;text-transform:uppercase;color:#333;align-items:center}
.main-nav .active{color:var(--green)}

/* hero */
.hero{position:absolute;top:120px;left:0;width:1200px;height:558px;background:
  linear-gradient(90deg,rgba(40,40,40,.45) 0%,rgba(40,40,40,.1) 45%,rgba(0,0,0,0) 60%),
  linear-gradient(90deg,#8e8a86 0%,#b3aea9 35%,#7b8aa0 62%,#2f5fb0 75%,#3b4350 100%)}
.hero-caption{position:absolute;left:125px;top:218px;color:#fff}
.hero-caption h1{font-family:"Roboto Condensed",sans-serif;font-weight:700;font-size:46px;text-transform:uppercase;line-height:1}
.hero-caption p{font-size:15px;margin-top:12px;width:380px;line-height:1.3}
.btn-yellow{display:inline-block;margin-top:22px;background:var(--yellow);color:#222;font-family:"Roboto Condensed",sans-serif;font-size:14px;text-transform:uppercase;padding:8px 20px}
.hero-arrow{position:absolute;top:268px}

/* intro */
.intro{position:absolute;top:678px;left:0;width:1200px;height:432px}
.intro-photo{position:absolute;left:100px;top:68px;width:378px;height:290px;border:2px solid #ddd;background:linear-gradient(90deg,#eef1f3 0%,#dfe4e7 40%,#3a3a3a 60%,#e9ecee 85%)}
.intro-text{position:absolute;left:510px;top:70px;width:590px}
.intro-text h2{font-size:34px}
.intro-text p{font-size:11.5px;line-height:1.75;color:var(--muted);margin-top:16px}
.btn-green{display:inline-block;background:var(--green);color:#fff;font-family:"Roboto Condensed",sans-serif;font-size:14px;text-transform:uppercase;padding:8px 26px;margin-top:24px}

/* services */
.services{position:absolute;top:1110px;left:0;width:1200px;height:560px;background:linear-gradient(180deg,#236f3d,#1c6433)}
.services h2{color:#fff;text-align:center;font-size:32px;margin-top:65px}
.services .lead{color:#fff;text-align:center;font-size:12px;line-height:1.7;width:760px;margin:10px auto 0}
.service-card{position:absolute;top:247px;width:323px;height:233px;background:#fff;text-align:center}
.service-icon{position:absolute;left:107px;top:-56px;width:110px;height:110px;border-radius:50%;background:var(--green);border:6px solid #fff;display:flex;align-items:center;justify-content:center}
.service-card h3{font-family:"Roboto Condensed",sans-serif;font-weight:400;font-size:21px;color:#333;margin-top:70px}
.service-card p{font-size:11px;line-height:1.8;color:var(--muted);width:270px;margin:12px auto 0}
.learn-more{display:inline-block;margin-top:18px;border-top:1px solid var(--green);padding-top:8px;font-family:"Roboto Condensed",sans-serif;font-size:13px;color:var(--green);text-transform:uppercase;width:84px}

/* blog */
.blog{position:absolute;top:1670px;left:0;width:1200px;height:534px}
.section-title{text-align:center;font-size:32px;padding-top:68px}
.section-rule{width:92px;height:2px;background:var(--green);margin:14px auto 0}
.post{position:absolute;top:150px;width:314px}
.post-photo{height:162px}
.post h3{font-family:"Open Sans",sans-serif;font-weight:400;font-size:15px;color:#333;margin-top:22px}
.post-meta{display:flex;gap:28px;font-size:11.5px;font-style:italic;color:#555;margin-top:12px}
.post-meta span{display:flex;gap:8px;align-items:center}
.post p{font-size:11px;line-height:1.75;color:var(--muted);margin-top:14px}

/* testimonials */
.testimonials{position:absolute;top:2204px;left:0;width:1200px;height:420px;background:var(--light)}
.testimonial{position:absolute;top:170px;width:450px;display:flex;gap:22px}
.avatar{flex:none;width:118px;height:118px;border-radius:50%;background:linear-gradient(180deg,#f4f4f4 0%,#e6e6e6 55%,#2b3342 70%,#1e2430 100%);border:5px solid #fff}
.quote{font-size:11.5px;font-style:italic;line-height:1.7;color:#444;padding-top:6px}
.stars{color:var(--yellow);font-size:12px;margin-top:6px;font-style:normal}
.stars b{color:#bbb;font-weight:400}
.cite{font-size:12px;font-style:italic;color:#444;margin-top:6px}
.pager{position:absolute;top:347px;left:567px;display:flex;gap:5px}
.pager i{width:14px;height:14px;border-radius:50%;border:1.5px solid #999;display:block}
.pager i.on{border-color:var(--green)}

/* footer */
.site-footer{position:absolute;top:2624px;left:0;width:1200px;height:293px;background:var(--footer);color:#fff}
.footer-col{position:absolute;top:52px}
.footer-col h4{font-family:"Roboto Condensed",sans-serif;font-weight:400;font-size:17px;text-transform:uppercase}
.contact-list{list-style:none;margin-top:22px;font-size:12.5px;line-height:1.6}
.contact-list li{display:flex;gap:14px;margin-bottom:16px}
.map{width:278px;height:140px;margin-top:18px;background:linear-gradient(135deg,#e2e2e2,#c4c4c4)}
.newsletter p{font-size:11.5px;line-height:1.7;margin-top:14px;width:240px}
.news-input{width:244px;height:40px;background:#fff;margin-top:14px;color:#666;font-size:11px;padding:12px 12px}
.news-btn{display:inline-block;margin-top:12px;background:var(--green);color:#fff;font-size:12px;font-family:"Roboto Condensed",sans-serif;text-transform:uppercase;padding:10px 16px}
.quick-links{list-style:none;margin-top:22px;font-size:12px;text-transform:uppercase}
.quick-links li{margin-bottom:13px;display:flex;gap:10px;align-items:center}
.quick-links li::before{content:"";border-left:5px solid #fff;border-top:4px solid transparent;border-bottom:4px solid transparent}
.bottom-bar{position:absolute;top:2917px;left:0;width:1200px;height:53px;background:var(--green-dark);color:#fff;font-size:12px;display:flex;align-items:center;padding:0 100px;justify-content:space-between}
.bottom-social{display:flex;gap:10px}
.bottom-social i{width:26px;height:26px;border-radius:50%;background:#fff;display:block}
</style>
</head>
<body>

<header class="site-header">
  <div class="brand"><span class="brand-mark"></span><span class="brand-name">VORELAN</span></div>
  <div class="topbar">
    <span><svg width="12" height="12" viewBox="0 0 24 24"><path fill="#333" d="M6.6 10.8a15 15 0 0 0 6.6 6.6l2.2-2.2c.3-.3.7-.4 1-.2 1.1.4 2.3.6 3.6.6.6 0 1 .4 1 1V20c0 .6-.4 1-1 1A17 17 0 0 1 3 4c0-.6.4-1 1-1h3.5c.6 0 1 .4 1 1 0 1.3.2 2.5.6 3.6.1.3 0 .7-.2 1z"/></svg>Call now for more information 1300 874 602</span>
    <span><svg width="13" height="10" viewBox="0 0 26 20"><rect x="1" y="1" width="24" height="18" fill="none" stroke="#333" stroke-width="2"/><path d="M1 1l12 10L25 1" fill="none" stroke="#333" stroke-width="2"/></svg>info@vorelan.com</span>
    <span class="social-dots"><i></i><i></i><i></i><i></i></span>
  </div>
  <nav class="main-nav">
    <a class="active">Home</a><a>About Us</a><a>Services</a><a>Blog</a><a>Videos</a><a>Contact Us</a>
    <svg width="13" height="13" viewBox="0 0 24 24"><circle cx="10" cy="10" r="7" fill="none" stroke="#333" stroke-width="3"/><path d="M15 15l7 7" stroke="#333" stroke-width="3"/></svg>
  </nav>
</header>

<section class="hero" role="img" aria-label="Personal trainer holding a tablet in a busy gym">
  <svg class="hero-arrow" style="left:34px" width="24" height="50" viewBox="0 0 24 50"><path d="M22 2L2 25l20 23" fill="none" stroke="#fff" stroke-width="2" opacity=".7"/></svg>
  <svg class="hero-arrow" style="right:34px" width="24" height="50" viewBox="0 0 24 50"><path d="M2 2l20 23L2 48" fill="none" stroke="#fff" stroke-width="2" opacity=".7"/></svg>
  <div class="hero-caption">
    <h1>Personal Training</h1>
    <p>Nemo enim ipsam voluptatem quia voluptas sit asper aut odit aut fugit, sed quia consequuntur</p>
    <a class="btn-yellow">Read More Info</a>
  </div>
</section>

<section class="intro">
  <div class="intro-photo" role="img" aria-label="Smiling trainer with towel and clipboard beside an exercise bike"></div>
  <div class="intro-text">
    <h2 class="heading">Personal Training in Vorelan</h2>
    <p>Nemo enim ipsam voluptatem quia voluptas sit aspernatur aut odit aut fugit, sed quia consequuntur magni dolores eos qui ratione voluptatem sequi nesciunt. Neque porro quisquam est, qui dolorem ipsum quia dolor sit amet, consectetur, adipisci velit, sed quia non numquam eius modi tempora incidunt ut labore et dolore magnam aliquam quaerat voluptatem. Ut enim ad minima veniam, quis nostrum exercitationem ullam corporis suscipit laboriosam, nisi ut aliquid ex ea commodi consequatur? Quis autem vel eum iure reprehenderit qui in ea voluptate velit esse quam nihil molestiae consequatur, vel illum qui</p>
    <p>Nemo enim ipsam voluptatem quia voluptas sit aspernatur aut odit aut fugit, sed quia consequuntur magni dolores eos qui ratione voluptatem sequi nesciunt. Neque porro quisquam</p>
    <a class="btn-green">Read More</a>
  </div>
</section>

<section class="services">
  <h2 class="heading">Personal Training Services</h2>
  <p class="lead">Nemo enim ipsam voluptatem quia voluptas sit aspernatur aut odit aut fugit, sed quia consequuntur magni dolores eos qui ratione voluptatem sequi nesciunt. Neque porro quisquam est, qui dolorem ipsum quia dolor sit amet, consectetur,</p>

  <article class="service-card" style="left:99px">
    <div class="service-icon"><svg width="50" height="50" viewBox="0 0 50 50" fill="#fff"><circle cx="25" cy="10" r="5"/><path d="M21 17h8v14l3 15h-4l-3-12-3 12h-4l3-15z"/><rect x="4" y="18" width="42" height="3"/><rect x="3" y="14" width="4" height="11"/><rect x="43" y="14" width="4" height="11"/></svg></div>
    <h3>Personal Training</h3>
    <p>Nemo enim ipsam voluptatem quia voluptas sit aspernatur aut odit aut fugit, sed quia consequuntur magni dolores eos qui ratione voluptatem</p>
    <a class="learn-more">Learn More</a>
  </article>
  <article class="service-card" style="left:438px">
    <div class="service-icon"><svg width="52" height="30" viewBox="0 0 52 30" fill="#fff"><rect x="2" y="11" width="5" height="8"/><rect x="8" y="3" width="7" height="24" rx="1"/><rect x="15" y="12" width="22" height="6"/><rect x="37" y="3" width="7" height="24" rx="1"/><rect x="45" y="11" width="5" height="8"/></svg></div>
    <h3>Fitness</h3>
    <p>Nemo enim ipsam voluptatem quia voluptas sit aspernatur aut odit aut fugit, sed quia consequuntur magni dolores eos qui ratione voluptatem</p>
    <a class="learn-more">Learn More</a>
  </article>
  <article class="service-card" style="left:778px">
    <div class="service-icon"><svg width="50" height="50" viewBox="0 0 50 50" fill="#fff"><circle cx="25" cy="9" r="5"/><path d="M25 16c-5 0-7 3-7 7v8l-9 5 2 3 11-5v-9h6v9l11 5 2-3-9-5v-8c0-4-2-7-7-7z"/><path d="M8 42h34v3H8z"/></svg></div>
    <h3>Outdoor Bootcamp Class</h3>
    <p>Nemo enim ipsam voluptatem quia voluptas sit aspernatur aut odit aut fugit, sed quia consequuntur magni dolores eos qui ratione voluptatem</p>
    <a class="learn-more">Learn More</a>
  </article>
</section>

<section class="blog">
  <h2 class="heading section-title">Vorelan Blog</h2>
  <div class="section-rule"></div>

  <article class="post" style="left:99px">
    <div class="post-photo" role="img" aria-label="Trainer assisting a client with a weight exercise" style="background:linear-gradient(180deg,#6b6b6b 0%,#3a3a3a 55%,#1e1e1e 100%)"></div>
    <h3>Nemo enim ipsam voluptatem quia</h3>
    <div class="post-meta">
      <span><svg width="11" height="11" viewBox="0 0 12 12"><rect x="1" y="2" width="10" height="9" fill="none" stroke="#888" stroke-width="1.3"/><path d="M1 5h10M4 1v2M8 1v2" stroke="#888" stroke-width="1.3"/></svg>March 25, 2015</span>
      <span><svg width="12" height="11" viewBox="0 0 12 11"><path d="M1 1h10v6H5l-3 3V7H1z" fill="none" stroke="#888" stroke-width="1.2"/></svg>No comments</span>
    </div>
    <p>Lorem ipsum dolor sit amet, consectetur adipisicing elit, sed do eiusmod tempor incididunt ut labore et dolore magna aliqua. Ut enim ad minim veniam,</p>
  </article>
  <article class="post" style="left:443px">
    <div class="post-photo" role="img" aria-label="Couple stretching outdoors on grass" style="background:linear-gradient(180deg,#9fc170 0%,#c9d9b0 35%,#7fae4c 70%,#5f9135 100%)"></div>
    <h3>Nemo enim ipsam voluptatem quia</h3>
    <div class="post-meta">
      <span><svg width="11" height="11" viewBox="0 0 12 12"><rect x="1" y="2" width="10" height="9" fill="none" stroke="#888" stroke-width="1.3"/><path d="M1 5h10M4 1v2M8 1v2" stroke="#888" stroke-width="1.3"/></svg>March 25, 2015</span>
      <span><svg width="12" height="11" viewBox="0 0 12 11"><path d="M1 1h10v6H5l-3 3V7H1z" fill="none" stroke="#888" stroke-width="1.2"/></svg>No comments</span>
    </div>
    <p>Lorem ipsum dolor sit amet, consectetur adipisicing elit, sed do eiusmod tempor incididunt ut labore et dolore magna aliqua. Ut enim ad minim veniam,</p>
  </article>
  <article class="post" style="left:787px">
    <div class="post-photo" role="img" aria-label="Trainer reviewing a plan with a client in a gym" style="background:linear-gradient(180deg,#4e5f78 0%,#8a93a0 50%,#3c4658 100%)"></div>
    <h3>Nemo enim ipsam voluptatem quia</h3>
    <div class="post-meta">
      <span><svg width="11" height="11" viewBox="0 0 12 12"><rect x="1" y="2" width="10" height="9" fill="none" stroke="#888" stroke-width="1.3"/><path d="M1 5h10M4 1v2M8 1v2" stroke="#888" stroke-width="1.3"/></svg>March 25, 2015</span>
      <span><svg width="12" height="11" viewBox="0 0 12 11"><path d="M1 1h10v6H5l-3 3V7H1z" fill="none" stroke="#888" stroke-width="1.2"/></svg>No comments</span>
    </div>
    <p>Lorem ipsum dolor sit amet, consectetur adipisicing elit, sed do eiusmod tempor incididunt ut labore et dolore magna aliqua. Ut enim ad minim veniam,</p>
  </article>
</section>

<section class="testimonials">
  <h2 class="heading section-title" style="padding-top:72px">What Our Customers Are Saying About Us</h2>
  <div class="section-rule"></div>

  <div class="testimonial" style="left:99px">
    <div class="avatar" role="img" aria-label="Customer portrait"></div>
    <div class="quote">“ Lorem ipsum dolor sit amet, consectetur adipisicing elit, sed do eiusmod tempor incididunt ut labore et dolore magna aliqua. Ut enim ad minim veniam, quis nostrud
      <div class="stars">★★★<b>☆☆</b></div>
      <div class="cite">RENA</div>
    </div>
  </div>
  <div class="testimonial" style="left:645px">
    <div class="avatar" role="img" aria-label="Customer portrait"></div>
    <div class="quote">“ Lorem ipsum dolor sit amet, consectetur adipisicing elit, sed do eiusmod tempor incididunt ut labore et dolore magna aliqua. Ut enim ad minim veniam, quis nostrud
      <div class="stars">★★★<b>☆☆</b></div>
      <div class="cite">JOHN DOE</div>
    </div>
  </div>
  <div class="pager"><i class="on"></i><i></i><i></i><i></i></div>
</section>

<footer class="site-footer">
  <div class="footer-col" style="left:99px;width:220px">
    <h4>Contact Us</h4>
    <ul class="contact-list">
      <li><svg width="14" height="18" viewBox="0 0 14 18" style="flex:none"><path d="M7 1a6 6 0 0 0-6 6c0 4 6 10 6 10s6-6 6-10a6 6 0 0 0-6-6z" fill="none" stroke="#fff" stroke-width="1.5"/><circle cx="7" cy="7" r="2" fill="#fff"/></svg>Suite 4, Level 2|28 Alder Crest Road|Fernhollow VIC 3190</li>
      <li><svg width="14" height="14" viewBox="0 0 24 24" style="flex:none"><path fill="#fff" d="M6.6 10.8a15 15 0 0 0 6.6 6.6l2.2-2.2c.3-.3.7-.4 1-.2 1.1.4 2.3.6 3.6.6.6 0 1 .4 1 1V20c0 .6-.4 1-1 1A17 17 0 0 1 3 4c0-.6.4-1 1-1h3.5c.6 0 1 .4 1 1 0 1.3.2 2.5.6 3.6.1.3 0 .7-.2 1z"/></svg>Phone : 1300 874 603</li>
      <li><svg width="16" height="12" viewBox="0 0 26 20" style="flex:none"><rect x="1" y="1" width="24" height="18" fill="none" stroke="#fff" stroke-width="2"/><path d="M1 1l12 10L25 1" fill="none" stroke="#fff" stroke-width="2"/></svg>support@vorelan.com.au</li>
    </ul>
  </div>
  <div class="footer-col" style="left:365px">
    <h4>Our Location</h4>
    <div class="map" role="img" aria-label="Street map of the studio location"></div>
  </div>
  <div class="footer-col newsletter" style="left:697px">
    <h4>Join Our Newsletter</h4>
    <p>Excepteur sint occaecat cupidatat non proident, sunt in culpa qui</p>
    <div class="news-input">Enter Name</div>
    <a class="news-btn">Subscribe</a>
  </div>
  <div class="footer-col" style="left:993px">
    <h4>Quick Links</h4>
    <ul class="quick-links"><li>Home</li><li>About</li><li>Services</li><li>Blog</li><li>Videos</li><li>Contact</li></ul>
  </div>
</footer>
<div class="bottom-bar">
  <span>Copyright 2016 | All Rights Reserved – Vorelan</span>
  <span class="bottom-social"><i></i><i></i><i></i><i></i></span>
</div>

</body>
</html>
```